Velmor Biologics product brochure - credibility, sophistication, cutting-edge

Velmor Biologics, Inc. is a company that provides the most cutting-edge regenerative medicine products in the US. This brochure will highlight our stem cell products VelmorBase and VelmorLink, educating the public/patients and physician alike on what stem cells are, comparison of various stem cell treatments available, and what makes Velmor products different. This serves as a marketing tool to reach both patients and physicians.

I have included the current brochure, which I am not completely happy with. I want a brochure that portrays that we are a top-notch company, with credibility and sophistication. I will make slight content change, but most contents will stay.

Please refer to current website for further information: www.velmorbiologics-example.com

Low design quality

Target Market(s)

doctors and patients.

Industry/Entity Type

Healthcare

Font styles to use
Serif
Other font styles liked:
• anything that looks best on brochures & easy to read

Colors

Designer to choose colors to be used in the design.

Requirements
Must have
• Clean & modern feel, eye-catching.
• Would prefer bi-fold rather than tri-fold, because I think it looks fresher.
• Easy to read, clear.
• beautiful, elegant, stunning
Should not have
• Please DO NOT recycle graphics or images from the old brochure. I would like this for sure to be brand new, fresh and original.

```html
<!DOCTYPE html>
<html lang="en">
<head>
<meta charset="utf-8">
<title>Velmor Biologics Brochure Cover</title>
<link rel="stylesheet" href="https://fonts.googleapis.com/css2?family=Montserrat:wght@300;600&display=swap">
<style>
  :root {
    --page-bg: #e6e6e6;
    --cover-bg: #f4f4f4;
    --gold: #c9963e;
    --gold-soft: #d8ac6a;
    --grey-dark: #5e5e5e;
    --grey-mid: #9a9a9a;
    --grey-light: #d2d2d2;
    --white: #ffffff;
  }
  html, body {
    margin: 0;
    padding: 0;
    width: 1200px;
    height: 960px;
    overflow: hidden;
    background: var(--page-bg);
    font-family: "Montserrat", sans-serif;
  }
  .brochure-cover {
    position: absolute;
    left: 160px;
    top: 40px;
    width: 880px;
    height: 880px;
    background: var(--cover-bg);
    overflow: hidden;
  }
  .cover-photo {
    position: absolute;
    left: 0;
    right: 0;
    top: 200px;
    bottom: 0;
    background:
      linear-gradient(180deg, var(--cover-bg) 0%, rgba(244,244,244,0) 28%),
      linear-gradient(100deg, var(--grey-light) 0%, var(--grey-mid) 22%, var(--grey-dark) 40%, var(--grey-mid) 52%, var(--gold-soft) 62%, var(--gold) 82%, var(--gold-soft) 100%);
  }
  .brand {
    position: absolute;
    top: 80px;
    left: 0;
    right: 0;
    display: flex;
    align-items: center;
    justify-content: center;
    gap: 12px;
  }
  .brand-mark {
    width: 22px;
    height: 22px;
    border-radius: 50%;
    background: var(--gold);
  }
  .brand-name {
    font-weight: 600;
    font-size: 22px;
    letter-spacing: 3px;
    text-transform: uppercase;
    color: var(--gold);
  }
  .tagline {
    position: absolute;
    left: 130px;
    top: 560px;
    margin: 0;
    font-weight: 300;
    font-size: 38px;
    letter-spacing: 2px;
    text-transform: uppercase;
    color: var(--white);
    white-space: nowrap;
  }
</style>
</head>
<body>
  <main class="brochure-cover">
    <div class="cover-photo" role="img" aria-label="Close-up photo of a wet grey apple being painted gold with a brush"></div>
    <header class="brand">
      <span class="brand-mark"></span>
      <span class="brand-name">Velmor Biologics, Inc</span>
    </header>
    <h1 class="tagline">Let the joy of healing begin</h1>
  </main>
</body>
</html>
```